I need a design that promotes "A peak path hub for runners". services include assessment, massage, physiotherapy, pilates, suspension training, kinesiotaping in any combination.
I would like to bring the design into my website, flyers etc

Target Market(s)

athletes from beginner to elite - any age, male and female

Industry/Entity Type

Shop

Contact Information for Business Card

Peak-Path Hub for Runners
17 Corla Lane, Westmere, Tauranga
021 874 3061
tess.harlow@mailbrook.example

Logo Text

Logo styles of interest
Abstract Logo
Requirements
Nice to have
• Blue colour theme

```html
<!DOCTYPE html>
<html lang="en">
<head>
<meta charset="utf-8">
<title>Peak-Path Hub for Runners – Business Card</title>
<link href="https://fonts.googleapis.com/css2?family=Orbitron:wght@600&family=Arimo:wght@400&display=swap" rel="stylesheet">
<style>
  :root {
    --page-bg: #e9e7e4;
    --navy-light: #3b4794;
    --navy-mid: #2b3277;
    --navy-dark: #1f2460;
    --band-light: #ffffff;
    --band-edge: #e2e2e2;
    --ink-navy: #2a2f6e;
    --ink-white: #f2f3fa;
  }
  * { margin: 0; padding: 0; box-sizing: border-box; }
  html, body {
    width: 1200px; height: 1181px; overflow: hidden;
    background: var(--page-bg);
  }
  .card {
    position: absolute;
    left: 212px;
    width: 776px; height: 446px;
    border-radius: 30px;
    overflow: hidden;
    background: radial-gradient(ellipse 420px 300px at 50% 40%, var(--navy-light) 0%, var(--navy-mid) 55%, var(--navy-dark) 100%);
    box-shadow: 0 6px 14px rgba(0,0,0,0.35);
  }
  .card--front { top: 105px; }
  .card--back { top: 620px; }
  .band {
    position: absolute;
    left: 0; top: 158px;
    width: 100%; height: 130px;
    background: radial-gradient(ellipse 360px 110px at 50% 45%, var(--band-light) 0%, #f5f5f5 45%, var(--band-edge) 100%);
    box-shadow: 0 3px 5px rgba(0,0,0,0.35);
    display: flex; align-items: center; justify-content: center;
  }
  .tagline {
    font-family: "Orbitron", sans-serif;
    font-weight: 600;
    font-size: 21px;
    letter-spacing: 8px;
    color: var(--ink-navy);
    text-transform: uppercase;
    text-shadow: 1px 2px 3px rgba(0,0,0,0.35);
    white-space: nowrap;
  }
  .services, .address {
    position: absolute;
    left: 0; width: 100%;
    text-align: center;
    font-family: "Arimo", sans-serif;
    font-size: 15px;
    line-height: 18px;
    letter-spacing: -0.3px;
    color: var(--ink-white);
  }
  .services { top: 399px; }
  .address { top: 417px; }
  .contacts {
    display: flex;
    justify-content: center;
    gap: 34px;
    font-family: "Arimo", sans-serif;
    font-size: 14.5px;
    letter-spacing: -0.4px;
    color: var(--ink-navy);
    text-shadow: 1px 1px 2px rgba(0,0,0,0.25);
    white-space: nowrap;
  }
  .contact { display: flex; align-items: center; gap: 6px; }
  .contact__mark {
    width: 8px; height: 8px;
    background: var(--ink-navy);
    display: inline-block;
  }
</style>
</head>
<body>
  <section class="card card--front">
    <div class="band">
      <h1 class="tagline">Peak - Path Hub for Runners</h1>
    </div>
    <p class="services">Assessment, - Massage - Physiotherapy - Pilates -<br>Suspension training - Kinesiotaping in any combination.</p>
  </section>

  <section class="card card--back">
    <div class="band">
      <div class="contacts">
        <span class="contact">Phone <i class="contact__mark"></i> 021 874 3061</span>
        <span class="contact">Web <i class="contact__mark"></i> www.peakpathhub.example</span>
        <span class="contact">Email <i class="contact__mark"></i> tess.harlow@mailbrook.example</span>
      </div>
    </div>
    <p class="address">17 Corla Lane, Westmere, Tauranga</p>
  </section>
</body>
</html>
```